Website for my photography business

I need a website for my photography business, Bram Kellet Photography. I need a website that has a landing page with a cover photo of each kind of photography I do. For example, Nature, Weddings, Portraits and Architecture. I want it so that when someone comes onto my website they have to choose which kind of photography page they want to visit. So if they click on the wedding photo it will open to a page with my wedding portfolio images and a contact me button. If they choose nature photography I want them to be redirected to an e-commerce section where they can purchase prints. Architecture and Portraits should open up to their respective portfolios with about me and contact info. I like this kind of format because I want people who come to my website for a specific type of photography to be able to be directed there easily without having to look at a mix of other kinds of photography. I will provide a few files to use as placeholders. I have already purchased the bramkelletphotography.example domain name. A Wix website would be great because I am most familiar with it but I am open to anything.

Industry/Entity Type

Photographer

Number of Pages Required

5+ page

Requirements
Must have
• Landing Page and e-commerce

```html
<!DOCTYPE html>
<html lang="en">
<head>
<meta charset="UTF-8">
<title>Bram Kellet Photography — Book a Session</title>
<link rel="stylesheet" href="https://fonts.googleapis.com/css2?family=Playfair+Display:wght@400&family=EB+Garamond:ital,wght@1,400&family=Jost:wght@300;400&display=swap">
<style>
  :root {
    --header-bg: #f7f7f7;
    --page-bg: #ffffff;
    --ink: #2b2b2b;
    --ink-soft: #444444;
    --muted: #777777;
    --card-border: #cfcfcf;
    --button-bg: #282828;
    --button-text: #ffffff;
    --icon: #111111;
    --wedding-a: #c9d2d6;
    --wedding-b: #5c6470;
    --portrait-a: #9fc4cc;
    --portrait-b: #3a2a24;
  }
  * { box-sizing: border-box; margin: 0; padding: 0; }
  html, body {
    width: 1200px; height: 765px; overflow: hidden;
    background: var(--page-bg); color: var(--ink);
  }
  .page { position: relative; width: 1200px; height: 765px; }

  .site-header {
    position: absolute; left: 0; top: 0; width: 1200px; height: 184px;
    background: var(--header-bg);
  }
  .brand-name {
    position: absolute; left: 0; top: 33px; width: 1200px; text-align: center;
    font-family: "Playfair Display", serif; font-weight: 400;
    font-size: 30px; line-height: 36px; letter-spacing: 2px; color: var(--ink);
  }
  .brand-tag {
    position: absolute; left: 0; top: 75px; width: 1200px; text-align: center;
    font-family: "Jost", sans-serif; font-weight: 300;
    font-size: 12px; line-height: 16px; letter-spacing: 8px; color: var(--ink-soft);
  }
  .main-nav a {
    position: absolute; top: 129px; transform: translateX(-50%);
    font-family: "EB Garamond", serif; font-style: italic;
    font-size: 15px; line-height: 20px; color: var(--ink); text-decoration: none; white-space: nowrap;
  }
  .main-nav a.is-current { color: var(--muted); }

  .section-title {
    position: absolute; left: 0; top: 206px; width: 1200px; text-align: center;
    font-family: "EB Garamond", serif; font-style: italic; font-weight: 400;
    font-size: 28px; line-height: 36px; color: var(--ink-soft);
  }

  .service-card {
    position: absolute; top: 271px; width: 262px; height: 376px;
    border: 1px solid var(--card-border); background: var(--page-bg); text-align: center;
  }
  .service-photo { width: 100%; height: 175px; }
  .service-photo.wedding { background: linear-gradient(160deg, var(--wedding-a) 30%, var(--wedding-b)); }
  .service-photo.portrait { background: linear-gradient(110deg, var(--portrait-a) 15%, #c48a72 55%, var(--portrait-b)); }
  .service-name {
    margin-top: 27px;
    font-family: "EB Garamond", serif; font-style: italic; font-weight: 400;
    font-size: 21px; line-height: 26px; color: var(--ink-soft);
  }
  .service-meta {
    font-family: "Jost", sans-serif; font-weight: 300; font-size: 12.5px; line-height: 16px; color: var(--ink-soft);
  }
  .service-duration { margin-top: 13px; }
  .service-price { margin-top: 12px; }
  .book-button {
    display: block; margin: 18px auto 0; width: 116px; height: 33px; line-height: 33px;
    background: var(--button-bg); color: var(--button-text);
    font-family: "Jost", sans-serif; font-weight: 400; font-size: 13px; text-decoration: none;
  }

  .social-links {
    position: absolute; top: 703px; left: 527px; display: flex; gap: 32px;
  }
  .social-link {
    display: block; width: 12px; height: 12px; border-radius: 3px;
    border: 1.5px solid var(--icon);
  }
  .copyright {
    position: absolute; left: 0; top: 727px; width: 1200px; text-align: center;
    font-family: "Jost", sans-serif; font-weight: 300; font-size: 12px; line-height: 16px; color: var(--muted);
  }
</style>
</head>
<body>
<div class="page">
  <header class="site-header">
    <div class="brand-name">BRAM KELLET</div>
    <div class="brand-tag">PHOTOGRAPHY</div>
    <nav class="main-nav">
      <a href="#" style="left:260px">Architecture</a>
      <a href="#" style="left:432px">Portraits</a>
      <a href="#" style="left:597px">Weddings</a>
      <a href="#" style="left:756px">Nature</a>
      <a href="#" class="is-current" style="left:931px">Book a Session</a>
    </nav>
  </header>

  <h1 class="section-title">Book a Session</h1>

  <article class="service-card" style="left:329px">
    <div class="service-photo wedding" role="img" aria-label="Bride and groom embracing outdoors under a grey sky"></div>
    <h2 class="service-name">Wedding Photography</h2>
    <p class="service-meta service-duration">2 hr 30 min</p>
    <p class="service-meta service-price">lei150</p>
    <a href="#" class="book-button">Book Now</a>
  </article>

  <article class="service-card" style="left:620px">
    <div class="service-photo portrait" role="img" aria-label="Portrait of a young woman in a black top against a soft blurred background"></div>
    <h2 class="service-name">Portrait Photography</h2>
    <p class="service-meta service-duration">2 hr 30 min</p>
    <p class="service-meta service-price">lei150</p>
    <a href="#" class="book-button">Book Now</a>
  </article>

  <nav class="social-links" aria-label="Social media links">
    <a href="#" class="social-link" aria-label="Social profile 1"></a>
    <a href="#" class="social-link" aria-label="Social profile 2"></a>
    <a href="#" class="social-link" aria-label="Social profile 3"></a>
    <a href="#" class="social-link" aria-label="Social profile 4"></a>
  </nav>
  <p class="copyright">© 2023 by Bram Kellet Photography</p>
</div>
</body>
</html>
```